Mobile Friendly Lead Generation Landing Page

We are a web marketing company that specialized in web lead generation. Recently we have started buying media from mobile devices and we need a mobile interface(landing page) where we can collect user data in an effective manner.

Our current mobile landing page is:
http://www.tutorpath.example.com/lp13d/index.aspx?a=true&source=841356
Through this you can see what the steps/questions users need to answer to get matched to a school. We need the design for the whole process.

We are pretty open for design ideas and our goal is to make this mobile optimized landing page have the look and feel of an app...but not an app.
There are several questions in the process but we are open to changing the way they are presented. As in, you can have one question at a time or a few.
The goal is to make this EXTREMELY EASY for users to interact with.

One example that we have liked is:
http://learnvane.example/schools/57214-page1.lvne (please note that this opens only on mobile devices)

Some of these screenshots are attached.

Our web form looks like this:
http://www.tutorpath.example.com/lp88/index.aspx?a=true

```html
<!DOCTYPE html>
<html lang="en">
<head>
<meta charset="utf-8">
<title>Field of Interest – Step Selection</title>
<link rel="stylesheet" href="https://fonts.googleapis.com/css2?family=Montserrat:wght@500;600;700&family=Roboto:wght@400;500&display=swap">
<style>
  :root {
    --page-bg: #eeeeee;
    --brand-green: #7fb200;
    --panel-white: #ffffff;
    --field-grey: #e3e3e3;
    --ink-dark: #222222;
    --ink-title: #333333;
    --status-ink: #111111;
  }
  * { box-sizing: border-box; margin: 0; padding: 0; }
  html, body {
    width: 1200px; height: 900px; overflow: hidden;
    background: var(--page-bg);
  }
  .screen {
    position: absolute; left: 442px; top: 128px;
    width: 352px; height: 625px;
    background: var(--brand-green);
    overflow: hidden;
  }
  .status-bar {
    position: absolute; left: 0; top: 0; width: 100%; height: 24px;
    background: var(--panel-white);
    font-family: "Roboto", Arial, sans-serif; font-size: 12.5px; color: var(--status-ink);
    display: flex; align-items: center; justify-content: space-between;
    padding: 0 6px 0 7px;
  }
  .status-left, .status-right { display: flex; align-items: center; gap: 4px; }
  .status-time { font-weight: 500; font-size: 13px; position: absolute; left: 50%; transform: translateX(-50%); }
  .address-area {
    position: absolute; left: 0; top: 24px; width: 100%; height: 46px;
    background: var(--panel-white);
  }
  .address-field {
    position: absolute; left: 8px; top: 6px; width: 336px; height: 30px;
    background: var(--field-grey); border-radius: 7px;
    font-family: "Roboto", Arial, sans-serif; font-size: 17px; color: var(--status-ink);
    display: flex; align-items: center; justify-content: flex-end; padding-right: 8px; gap: 6px;
    white-space: nowrap; overflow: hidden;
  }
  .top-bar { position: absolute; left: 0; top: 70px; width: 100%; height: 72px; }
  .back-button {
    position: absolute; left: 9px; top: 15px; width: 44px; height: 44px;
    border: 2px solid var(--panel-white); border-radius: 50%;
    display: flex; align-items: center; justify-content: center;
  }
  .progress-panel {
    position: absolute; left: 63px; top: 0; width: 289px; height: 72px;
    background: var(--panel-white);
    box-shadow: 0 4px 6px rgba(0,0,0,0.25);
  }
  .progress-track {
    position: absolute; left: 13px; top: 26px; width: 262px; height: 19px;
    border: 1.5px solid var(--brand-green); border-radius: 3px; overflow: hidden;
  }
  .progress-fill { position: absolute; left: 0; top: 0; width: 50%; height: 100%; background: var(--brand-green); }
  .progress-label {
    position: absolute; right: 18px; top: 2px;
    font-family: "Montserrat", Arial, sans-serif; font-size: 7.5px; font-weight: 500; color: var(--brand-green);
  }
  .question-title {
    position: absolute; left: 0; top: 168px; width: 100%; text-align: center;
    font-family: "Montserrat", Arial, sans-serif; font-weight: 700; font-size: 17px; color: var(--ink-title);
    letter-spacing: -0.2px;
  }
  .choice-list { position: absolute; left: 11px; top: 213px; width: 330px; list-style: none; }
  .choice {
    position: relative; height: 63px; margin-bottom: 3px;
    background: var(--panel-white);
    display: flex; align-items: center; justify-content: center;
    font-family: "Montserrat", Arial, sans-serif; font-weight: 600; font-size: 15px; color: var(--ink-dark);
  }
  .choice-label { padding-left: 2px; }
  .choice-chevron { position: absolute; right: 26px; top: 24px; }
</style>
</head>
<body>
  <main class="screen">
    <div class="status-bar">
      <div class="status-left">
        <svg width="36" height="8" viewBox="0 0 36 8" aria-hidden="true">
          <circle cx="4" cy="4" r="3.3" fill="#111"/><circle cx="11" cy="4" r="3.3" fill="#111"/>
          <circle cx="18" cy="4" r="3.3" fill="#111"/><circle cx="25" cy="4" r="3.3" fill="#111"/>
          <circle cx="32" cy="4" r="3" fill="none" stroke="#111" stroke-width="0.9"/>
        </svg>
        <span>Carrier</span>
        <svg width="15" height="11" viewBox="0 0 15 11" aria-hidden="true">
          <path d="M1 4 A9 9 0 0 1 14 4" fill="none" stroke="#111" stroke-width="1.6"/>
          <path d="M3.5 6.5 A5.5 5.5 0 0 1 11.5 6.5" fill="none" stroke="#111" stroke-width="1.6"/>
          <path d="M7.5 10.5 L5.6 8.4 A2.8 2.8 0 0 1 9.4 8.4 Z" fill="#111"/>
        </svg>
        <svg width="10" height="10" viewBox="0 0 10 10" aria-hidden="true">
          <g stroke="#555" stroke-width="1.3" stroke-linecap="round">
            <line x1="5" y1="0.8" x2="5" y2="3"/><line x1="5" y1="7" x2="5" y2="9.2"/>
            <line x1="0.8" y1="5" x2="3" y2="5"/><line x1="7" y1="5" x2="9.2" y2="5"/>
            <line x1="2" y1="2" x2="3.5" y2="3.5"/><line x1="6.5" y1="6.5" x2="8" y2="8"/>
            <line x1="8" y1="2" x2="6.5" y2="3.5"/><line x1="3.5" y1="6.5" x2="2" y2="8"/>
          </g>
        </svg>
      </div>
      <span class="status-time">12:34 AM</span>
      <div class="status-right">
        <svg width="8" height="12" viewBox="0 0 8 12" aria-hidden="true">
          <path d="M1 3.5 L6.5 8.5 L4 11 L4 1 L6.5 3.5 L1 8.5" fill="none" stroke="#111" stroke-width="1.2"/>
        </svg>
        <span>100%</span>
        <svg width="26" height="12" viewBox="0 0 26 12" aria-hidden="true">
          <rect x="0.5" y="0.5" width="22" height="11" rx="1.5" fill="none" stroke="#111"/>
          <rect x="2" y="2" width="19" height="8" fill="#111"/>
          <rect x="23.5" y="4" width="2" height="4" fill="#111"/>
        </svg>
      </div>
    </div>

    <div class="address-area">
      <div class="address-field">
        <span>http://www.tutorpath.example.com/</span>
        <svg width="16" height="16" viewBox="0 0 16 16" aria-hidden="true">
          <path d="M13 8 A5 5 0 1 1 10.5 3.7" fill="none" stroke="#111" stroke-width="1.8"/>
          <path d="M9 1 L13 3.8 L9 6.5 Z" fill="#111"/>
        </svg>
      </div>
    </div>

    <header class="top-bar">
      <div class="back-button" aria-label="Back">
        <svg width="14" height="18" viewBox="0 0 14 18" aria-hidden="true">
          <path d="M10 2 L3 9 L10 16" fill="none" stroke="#fff" stroke-width="2.4" stroke-linecap="round" stroke-linejoin="round"/>
        </svg>
      </div>
      <div class="progress-panel">
        <div class="progress-track">
          <div class="progress-fill"></div>
          <span class="progress-label">Amout completed</span>
        </div>
      </div>
    </header>

    <h1 class="question-title">Please select your field of interest</h1>

    <ul class="choice-list">
      <li class="choice"><span class="choice-label">Art and design</span><svg class="choice-chevron" width="10" height="15" viewBox="0 0 10 15" aria-hidden="true"><path d="M2 1.5 L8 7.5 L2 13.5" fill="none" stroke="#222" stroke-width="2"/></svg></li>
      <li class="choice"><span class="choice-label">Criminal Justice</span><svg class="choice-chevron" width="10" height="15" viewBox="0 0 10 15" aria-hidden="true"><path d="M2 1.5 L8 7.5 L2 13.5" fill="none" stroke="#222" stroke-width="2"/></svg></li>
      <li class="choice"><span class="choice-label">Educational and Teaching</span><svg class="choice-chevron" width="10" height="15" viewBox="0 0 10 15" aria-hidden="true"><path d="M2 1.5 L8 7.5 L2 13.5" fill="none" stroke="#222" stroke-width="2"/></svg></li>
      <li class="choice"><span class="choice-label">Health Care</span><svg class="choice-chevron" width="10" height="15" viewBox="0 0 10 15" aria-hidden="true"><path d="M2 1.5 L8 7.5 L2 13.5" fill="none" stroke="#222" stroke-width="2"/></svg></li>
      <li class="choice"><span class="choice-label">Human Services</span><svg class="choice-chevron" width="10" height="15" viewBox="0 0 10 15" aria-hidden="true"><path d="M2 1.5 L8 7.5 L2 13.5" fill="none" stroke="#222" stroke-width="2"/></svg></li>
      <li class="choice"><span class="choice-label">Psychology</span><svg class="choice-chevron" width="10" height="15" viewBox="0 0 10 15" aria-hidden="true"><path d="M2 1.5 L8 7.5 L2 13.5" fill="none" stroke="#222" stroke-width="2"/></svg></li>
    </ul>
  </main>
</body>
</html>
```